Business Cards for new orthopaedic surgery practice

My husband and I are starting our own orthopaedic surgery practice. We are looking for a business card that is uniform, but one will have my name/title and the other will have his. You can just create one design with my name on it for now. But when I choose your design as the winning design I will ask that you add another copy with his name/title.

We are looking for classy, simple, elite all in one. We like dark blues/a little gold/yellow. Something that goes with our logo. We want our logo incorporated. Here is all the info you need:
Business name: RV Bone & Vitality Center
Location: 38517 North Willowmere Ave
Maple Hollow, FL 33490
Phone: 954-218-4063
Fax: 954-582-7341
Email: info@myrvbonecare.example

Names: Lydia Vance, M.D.
Board Certified Hand and Upper Extremity Surgeon

Ebo Dansu, M.D.
Board Certified Hip & Knee Replacement/General Orthopaedic Surgeon

Can decide what you want to put on the back. Maybe a slogan:
Steady Hands. Lasting Strength

I am just going to upload our logo. The only thing is if we select you as the winning design, the location, and phone numbers may change. We will need your help to update that once fully solidified.

Industry/Entity Type

Medical

Contact Information for Business Card

Colors
0054AA
0677BA
7BADD7
CADEEF
E8F1F8
0094D4
00A9DD
6FCCEA
C7EBF8
E9F6FB

Requirements
Must have
• class, appeal,
Should not have
• We want to air on the side of masculine if we are looking at masculine vs. feminine feel. But we still want it classy, sophisticated, and something we will love

```html
<!DOCTYPE html>
<html lang="en">
<head>
<meta charset="utf-8">
<title>RV Bone &amp; Vitality Center – Business Card</title>
<link rel="stylesheet" href="https://fonts.googleapis.com/css2?family=Montserrat:wght@400;500;600;700&display=swap">
<style>
  :root {
    --page: #d8d4cf;
    --card: #eef0f1;
    --card-edge: #f8f9fa;
    --navy: #1b2a5c;
    --navy-deep: #14204a;
    --gold: #c9972f;
    --gold-text: #c4912c;
    --ink: #1e2740;
    --white: #ffffff;
    --faint: rgba(60, 70, 90, 0.16);
  }
  * { margin: 0; padding: 0; box-sizing: border-box; }
  html, body {
    width: 1200px; height: 887px; overflow: hidden;
    background: var(--page);
    font-family: "Montserrat", sans-serif;
  }
  .card {
    position: absolute; left: 100px; top: 163px;
    width: 1000px; height: 560px;
    background: var(--card);
    border: 2px solid var(--card-edge);
    border-radius: 26px;
    overflow: hidden;
  }
  .title-band {
    position: absolute; left: 0; top: 57px;
    width: 100%; height: 165px;
    background: linear-gradient(90deg, var(--navy-deep), var(--navy) 70%);
  }
  .title-band .gold-end {
    position: absolute; right: 0; top: 0;
    width: 92px; height: 100%;
    background: var(--gold);
  }
  .doctor-name {
    position: absolute; left: 60px; top: 90px;
    font-size: 35px; font-weight: 700; letter-spacing: 2px;
    color: var(--gold); white-space: nowrap;
  }
  .doctor-title {
    position: absolute; left: 60px; top: 136px;
    font-size: 21px; font-weight: 400; line-height: 27px;
    color: var(--white); letter-spacing: 0.5px;
  }
  .brand-mark {
    position: absolute; right: 60px; top: 60px;
    display: flex; align-items: center; gap: 16px;
  }
  .brand-mark .dot {
    width: 162px; height: 162px; border-radius: 50%;
    background: var(--white);
    order: 2;
  }
  .brand-mark .brand-name {
    font-size: 16px; font-weight: 600; line-height: 22px;
    color: var(--white); text-align: right;
    letter-spacing: 1px; text-transform: uppercase;
  }
  .contact-list {
    position: absolute; left: 56px; top: 278px;
    list-style: none;
  }
  .contact-list li {
    display: flex; align-items: center; gap: 8px;
    font-size: 21px; line-height: 28px; color: var(--ink);
  }
  .contact-list svg { width: 20px; height: 20px; flex: none; }
  .contact-list .accent { color: var(--gold-text); }
  .address {
    position: absolute; left: 56px; top: 403px;
    font-size: 21px; line-height: 27px; color: var(--ink);
  }
  .slogan {
    position: absolute; left: 56px; top: 472px;
    font-size: 20px; font-weight: 600; color: var(--gold-text);
  }
  .brand-watermark {
    position: absolute; right: 34px; top: 330px;
    width: 330px;
    font-size: 40px; font-weight: 700; line-height: 46px;
    color: var(--faint); text-align: right;
    text-transform: uppercase; letter-spacing: 1px;
  }
</style>
</head>
<body>
  <div class="card">
    <div class="title-band"><div class="gold-end"></div></div>
    <h1 class="doctor-name">LYDIA VANCE, M.D</h1>
    <p class="doctor-title">Board Certified Hand and<br>Upper Extremity Surgeon</p>

    <div class="brand-mark">
      <span class="dot"></span>
      <span class="brand-name">RV Bone &amp;<br>Vitality Center</span>
    </div>

    <ul class="contact-list">
      <li>
        <svg viewBox="0 0 20 20" aria-hidden="true"><path fill="#c9972f" d="M4 2l3 0 1.5 4-2 1.5c1 2.2 2.8 4 5 5l1.5-2 4 1.5v3c0 1-1 2-2 2C8.5 17 3 11.5 2 4c0-1 1-2 2-2z"/></svg>
        954-218-4063
      </li>
      <li>
        <svg viewBox="0 0 20 20" aria-hidden="true"><g fill="none" stroke="#c9972f" stroke-width="1.6"><rect x="5" y="2" width="10" height="5"/><rect x="2" y="7" width="16" height="7" rx="1"/><rect x="5" y="11" width="10" height="7"/></g></svg>
        954-582-7341
      </li>
      <li>
        <svg viewBox="0 0 20 20" aria-hidden="true"><g fill="none" stroke="#c9972f" stroke-width="1.6"><rect x="2" y="4" width="16" height="12"/><path d="M2 4l8 7 8-7"/></g></svg>
        info@myrvbonecare.example
      </li>
      <li>
        <svg viewBox="0 0 20 20" aria-hidden="true"><g fill="none" stroke="#c9972f" stroke-width="1.5"><circle cx="10" cy="10" r="8"/><ellipse cx="10" cy="10" rx="3.5" ry="8"/><path d="M2 10h16M3.5 6h13M3.5 14h13"/></g></svg>
        <span>www.<span class="accent">myrvbonecare</span>.example</span>
      </li>
    </ul>

    <p class="address">38517 North Willowmere Ave<br>Maple Hollow, FL 33490</p>
    <p class="slogan">Steady Hands. Lasting Strength</p>

    <div class="brand-watermark">RV Bone &amp; Vitality Center</div>
  </div>
</body>
</html>
```